TA BRAMLEY BUSINESS CARD DESIGN PROJECT

We need to utilize our logo that was expertly created on PixelHarbor and now need to match this with a business card design.

```html
<!DOCTYPE html>
<html lang="en">
<head>
<meta charset="utf-8">
<title>TA Bramley – Business Card</title>
<link href="https://fonts.googleapis.com/css2?family=Montserrat:wght@400;500;600;700&display=swap" rel="stylesheet">
<style>
  :root {
    --page-bg: #e6e0d8;
    --card-bg: #f3efea;
    --card-edge: #ded7ce;
    --brand-blue: #1f5497;
    --ink-blue: #1b4a86;
    --ink-dark: #2b2b2b;
  }
  * { margin: 0; padding: 0; box-sizing: border-box; }
  html, body {
    width: 1200px;
    height: 1047px;
    overflow: hidden;
    background: var(--page-bg);
    font-family: "Montserrat", sans-serif;
  }
  .canvas {
    position: relative;
    width: 1200px;
    height: 1047px;
  }
  .business-card {
    position: absolute;
    left: 120px;
    top: 261px;
    width: 960px;
    height: 524px;
    background: var(--card-bg);
    border: 1px solid var(--card-edge);
    border-radius: 22px;
    box-shadow: 0 10px 30px rgba(80, 60, 40, 0.12);
  }
  .brand-name {
    position: absolute;
    left: 40px;
    width: 460px;
    top: 232px;
    text-align: center;
    font-weight: 600;
    font-size: 44px;
    letter-spacing: 6px;
    color: var(--brand-blue);
  }
  .divider {
    position: absolute;
    left: 520px;
    top: 120px;
    width: 3px;
    height: 280px;
    background: var(--ink-blue);
  }
  .contact-block {
    position: absolute;
    left: 558px;
    top: 112px;
    color: var(--ink-dark);
  }
  .person-name {
    font-weight: 700;
    font-size: 31px;
    letter-spacing: 0.5px;
    color: var(--ink-blue);
    line-height: 1.1;
  }
  .person-title {
    font-size: 22px;
    font-weight: 400;
    margin-top: 4px;
  }
  .contact-list {
    list-style: none;
    margin-top: 20px;
  }
  .contact-list li {
    display: flex;
    align-items: center;
    gap: 8px;
    font-size: 22px;
    line-height: 30px;
  }
  .contact-icon {
    width: 20px;
    height: 20px;
    flex: none;
    fill: var(--ink-blue);
  }
  .address {
    font-size: 22px;
    line-height: 30px;
    margin-top: 16px;
  }
</style>
</head>
<body>
<div class="canvas">
  <div class="business-card">
    <div class="brand-name">TA BRAMLEY</div>
    <div class="divider"></div>
    <div class="contact-block">
      <div class="person-name">DANIEL HARTLEY</div>
      <div class="person-title">Managing Director</div>
      <ul class="contact-list">
        <li>
          <svg class="contact-icon" viewBox="0 0 20 20" aria-hidden="true"><path d="M2 7c0-2 3-4 8-4s8 2 8 4v2h-4V7H6v2H2z"/><rect x="4" y="10" width="12" height="7" rx="1.5"/></svg>
          <span>123 456 789</span>
        </li>
        <li>
          <svg class="contact-icon" viewBox="0 0 20 20" aria-hidden="true"><rect x="2" y="7" width="16" height="11" rx="1.5"/><rect x="5" y="2" width="8" height="6" fill="#f3efea" stroke="#1b4a86" stroke-width="1.5"/></svg>
          <span>123 456 789</span>
        </li>
        <li>
          <svg class="contact-icon" viewBox="0 0 20 20" aria-hidden="true"><rect x="2" y="5" width="16" height="11" rx="1"/><path d="M2 6l8 6 8-6" fill="none" stroke="#f3efea" stroke-width="1.5"/></svg>
          <span>info@youremail.com</span>
        </li>
        <li>
          <svg class="contact-icon" viewBox="0 0 20 20" aria-hidden="true"><circle cx="10" cy="10" r="8"/><path d="M6 6c2 1 2 3 4 3s1 3 3 4M12 4c0 2 2 2 3 3" fill="none" stroke="#f3efea" stroke-width="1.5"/></svg>
          <span>www.yourwebsite.com</span>
        </li>
      </ul>
      <div class="address">Your address, City<br>State, Zip 1234</div>
    </div>
  </div>
</div>
</body>
</html>
```